indépendant en tant que Massothérapeute et Préparateur Mental, j'ai besoin de ...

Massothérapeute et préparateur mental indépendant, je recherche une carte de visite sobre et dynamique, sans images liées au massage ou à la préparation mentale mais intégrant mon logo. Les couleurs que j'aime bien sont : Blanc, gris, anthracite, noir et jaune

Contact Information for Business Card

carte de préférence Horizontale
neutre qui puisse toucher le deux domaines Massothérapie et préparation mentale

Requirements
Must have
• mon projet doit intégrer au recto:
LOGO
Loïc Bardèze
078 513 26 48
info@loicbardeze.ch
et éventuellement www.loicbardeze.ch

et au verso les deux adresses:

Chemin des Ormilles 7B
1400 Yverdon-les-Bains

Route de la Gravière 9
1700 Fribourg

Should not have
• mon projet ne doit pas contenir d'image en liens avec le massage ni la préparation mentale.

```html
<!DOCTYPE html>
<html lang="fr">
<head>
<meta charset="utf-8">
<title>Loïc Bardèze – Cartes de visite</title>
<link rel="stylesheet" href="https://fonts.googleapis.com/css2?family=Montserrat:wght@500;600&family=Arimo&display=swap">
<style>
  :root {
    --stage: #161616;
    --kraft-light: #dfbf93;
    --kraft-mid: #c69c69;
    --kraft-dark: #a3744a;
    --ink: #1a1714;
    --rule: rgba(26, 23, 20, 0.45);
  }
  * { box-sizing: border-box; margin: 0; padding: 0; }
  html, body {
    width: 1093px; height: 1200px; overflow: hidden;
    background: var(--stage);
  }
  .canvas { position: relative; width: 1093px; height: 1200px; }
  .card {
    position: absolute; left: 264px; width: 580px; height: 357px;
    background: linear-gradient(135deg, var(--kraft-light) 0%, var(--kraft-mid) 50%, var(--kraft-dark) 100%);
    color: var(--ink);
  }
  .card--front { top: 226px; }
  .card--back { top: 620px; }

  .brand {
    position: absolute; left: 0; right: 0;
    display: flex; align-items: center; justify-content: center; gap: 14px;
  }
  .card--front .brand { top: 70px; }
  .card--back .brand { top: 124px; }
  .brand__mark { width: 34px; height: 34px; background: var(--ink); border-radius: 3px; }
  .brand__text { display: flex; flex-direction: column; }
  .brand__name {
    font-family: "Montserrat", sans-serif; font-weight: 600;
    font-size: 26px; line-height: 1; letter-spacing: 0.5px;
  }
  .brand__tagline {
    font-family: "Montserrat", sans-serif; font-weight: 500;
    font-size: 8.5px; letter-spacing: 0.8px; text-transform: uppercase;
    margin-top: 6px;
  }

  .holder {
    position: absolute; top: 178px; left: 0; right: 0; text-align: center;
    font-family: "Montserrat", sans-serif; font-weight: 600;
    font-size: 21px; letter-spacing: 0.3px; text-transform: uppercase;
  }
  .icon-row {
    position: absolute; top: 218px; left: 0; right: 0;
    display: flex; align-items: center; justify-content: center; gap: 4px;
  }
  .icon-row__rule { width: 52px; height: 1px; background: var(--rule); margin: 0 2px; }
  .icon { width: 24px; height: 24px; background: var(--ink); border-radius: 3px;
    display: flex; align-items: center; justify-content: center; }
  .icon svg { width: 16px; height: 16px; }

  .contact {
    position: absolute; top: 254px; left: 0; right: 0; text-align: center;
    font-family: "Arimo", sans-serif; font-size: 17px; line-height: 21px;
    list-style: none;
  }
  .addresses {
    position: absolute; top: 258px; left: 0; right: 0; text-align: center;
    font-family: "Arimo", sans-serif; font-size: 17px; line-height: 32px;
    font-style: normal;
  }
</style>
</head>
<body>
<main class="canvas">
  <section class="card card--front" aria-label="Recto">
    <div class="brand">
      <span class="brand__mark"></span>
      <div class="brand__text">
        <span class="brand__name">Loïc Bardèze</span>
        <span class="brand__tagline">Massothérapeute / Préparateur Mental</span>
      </div>
    </div>
    <h1 class="holder">Loïc Bardèze</h1>
    <div class="icon-row">
      <span class="icon-row__rule"></span>
      <span class="icon" aria-label="Téléphone">
        <svg viewBox="0 0 16 16"><path d="M2 6c0-2 3-3 6-3s6 1 6 3v1h-3V6H5v1H2z M4 8h8l1 5H3z" fill="var(--kraft-mid)"/><circle cx="8" cy="10.5" r="1.4" fill="var(--ink)"/></svg>
      </span>
      <span class="icon" aria-label="E-mail">
        <svg viewBox="0 0 16 16"><rect x="2" y="4" width="12" height="8" fill="none" stroke="var(--kraft-mid)" stroke-width="1.3"/><path d="M2 4l6 5 6-5" fill="none" stroke="var(--kraft-mid)" stroke-width="1.3"/></svg>
      </span>
      <span class="icon" aria-label="Site web">
        <svg viewBox="0 0 16 16"><circle cx="8" cy="8" r="6" fill="var(--kraft-mid)"/><path d="M5 5c2 0 3 1 2 3s1 3 0 4M10 4c0 2 2 2 3 3" fill="none" stroke="var(--ink)" stroke-width="1.2"/></svg>
      </span>
      <span class="icon-row__rule"></span>
    </div>
    <ul class="contact">
      <li>078 513 26 48</li>
      <li>info@loicbardeze.ch</li>
      <li>www.loicbardeze.ch</li>
    </ul>
  </section>

  <section class="card card--back" aria-label="Verso">
    <div class="brand">
      <span class="brand__mark"></span>
      <div class="brand__text">
        <span class="brand__name">Loïc Bardèze</span>
        <span class="brand__tagline">Massothérapeute / Préparateur Mental</span>
      </div>
    </div>
    <address class="addresses">
      Chemin des Ormilles 7B, 1400 Yverdon-les-Bains<br>
      Route de la Gravière 9, 1700 Freiburg
    </address>
  </section>
</main>
</body>
</html>
```